Brivo Australia Dental

I need to update my website and design. I have some ideas in mind and would like to replicate the format from another website into my own. I need the website to be easy to edit (I have no prior wordpress exp) after the design is complete. Please visit https://thelittlenestcare.org.au/ for example of layout.
Target Market(s)
Parents and elder folks
Industry/Entity Type
Dental
Coding
Coded - Design and coding required
Number of Pages Required
4 page
Font styles to use
Sans Serif
Colors
0392cd
Requirements
Must have
- - Home, Services, About Us, News
- - Colours
- - Clear action from viewers
- - Location of business (able to change all the time)
- - Illustrations/ photos

```html
<!DOCTYPE html>
<html lang="en">
<head>
<meta charset="utf-8">
<title>Brivo Australia Dental</title>
<link href="https://fonts.googleapis.com/css2?family=Lato:wght@400;700;900&display=swap" rel="stylesheet">
<style>
:root{
  --blue:#0392cd;
  --blue-dark:#0278ad;
  --ink:#222a33;
  --text:#4f5660;
  --grey:#7a7f86;
  --night:#16191d;
  --white:#ffffff;
}
*{margin:0;padding:0;box-sizing:border-box}
html,body{width:1200px;height:4580px;overflow:hidden}
body{font-family:'Lato',sans-serif;color:var(--text);background:var(--white);position:relative}
.abs{position:absolute}
a{color:inherit;text-decoration:none}

/* header */
.site-header{left:0;top:0;width:1200px;height:148px;background:var(--blue);color:var(--white)}
.brand{left:132px;top:44px;width:230px;font-size:27px;font-weight:700;line-height:32px}
.social{display:flex;gap:28px}
.social span{width:16px;height:16px;border-radius:50%;background:var(--white);display:block}
.header-social{left:620px;top:24px}
.call{left:910px;top:20px;display:flex;gap:14px;align-items:center}
.call-label{font-size:10px;letter-spacing:.5px}
.call-number{font-size:19px;font-weight:700}
.main-nav{left:390px;top:98px;display:flex;gap:40px;font-size:15px;font-weight:700}
.main-nav .current{color:var(--ink)}
.nav-donate{left:975px;top:95px;font-size:16px;font-weight:700;letter-spacing:.5px}

/* hero */
.hero-photo{left:0;top:148px;width:1200px;height:640px;background:linear-gradient(120deg,#cfc6bf 0%,#b8c6cf 35%,#7f95a6 65%,#dfe3e6 100%)}
.hero-title{left:0;top:305px;width:1200px;text-align:center;font-size:62px;font-weight:900;color:var(--blue);line-height:80px}
.btn-hero{left:512px;top:497px;width:176px;height:54px;background:var(--blue);color:var(--white);font-weight:700;font-size:17px;display:flex;align-items:center;justify-content:center}
.dots{left:568px;top:638px;display:flex;gap:8px}
.dots span{width:16px;height:16px;border:2px solid var(--white);background:var(--blue);border-radius:3px}

/* section headings */
.section-title{left:0;width:1200px;text-align:center;font-size:47px;font-weight:900;color:var(--ink)}
.section-title em{font-style:normal;color:var(--blue)}
.rule{left:563px;width:74px;height:4px;background:var(--grey)}

.mission-text{left:195px;top:962px;width:810px;text-align:center;font-size:13.5px;line-height:29px}
.pill{border-radius:30px;display:flex;align-items:center;justify-content:center;gap:12px;font-weight:700;font-size:16px}
.btn-mission{left:522px;top:1110px;width:165px;height:57px;background:var(--blue);color:var(--white)}

/* about */
.about-band{left:0;top:1255px;width:712px;height:575px;background:var(--blue)}
.about-photo{left:633px;top:1308px;width:567px;height:507px;border:3px solid var(--white);background:linear-gradient(135deg,#3fb8d8 0%,#9fd8e6 40%,#e9dcd4 70%,#f2f2f2 100%)}
.about-title{left:112px;top:1325px;font-size:47px;font-weight:900;color:var(--white)}
.about-title em{font-style:normal;color:var(--ink)}
.about-text{left:112px;top:1438px;width:490px;font-size:15px;line-height:28px;color:var(--white)}
.about-text p+p{margin-top:24px}
.btn-about{left:103px;top:1695px;width:163px;height:56px;background:var(--white);color:var(--blue)}

/* values */
.value{width:340px;text-align:center}
.value-photo{width:176px;height:176px;border-radius:50%;margin:0 auto;border-bottom:6px solid var(--blue);background:linear-gradient(160deg,#eaeef1,#9db3c2)}
.value h3{margin-top:40px;font-size:19px;font-weight:900;color:var(--blue)}
.value p{margin:16px auto 0;width:290px;height:78px;font-size:13px;line-height:26px}
.value .more{margin-top:24px;font-size:20px;font-weight:700;color:var(--blue);display:flex;justify-content:center;gap:8px;align-items:center}

/* donate band */
.donate-dark{left:0;top:2562px;width:805px;height:165px;background:var(--night)}
.donate-blue{left:805px;top:2562px;width:395px;height:165px;background:var(--blue)}
.donate-title{left:140px;top:2593px;font-size:27px;font-weight:700;color:var(--white)}
.donate-text{left:140px;top:2640px;width:560px;font-size:14.5px;line-height:28px;color:var(--white)}
.btn-donate{left:853px;top:2620px;width:215px;height:60px;background:var(--white);color:var(--blue);font-size:22px}

/* services */
.service-photo{width:436px;height:277px;border:3px solid var(--blue-dark)}
.service-title{font-size:30px;font-weight:700;color:var(--ink)}
.service-list{list-style:none;font-size:15px;line-height:23px}
.service-list li{position:relative;padding-left:40px;margin-bottom:20px}
.service-list svg{position:absolute;left:0;top:2px}

/* map & contact */
.map{left:0;top:3698px;width:1200px;height:620px;background:linear-gradient(180deg,#eef2f4,#e2eaee)}
.contact-card{left:685px;top:3722px;width:403px;height:520px;background:var(--white);box-shadow:0 0 0 2px #e4e8eb}
.card-title{width:403px;text-align:center;font-size:22px;font-weight:900;color:var(--blue)}
.hours{left:30px;top:112px;font-size:14.5px;color:var(--blue);line-height:36px}
.hours td{width:157px}
.contact-row{left:36px;display:flex;gap:20px;align-items:center;font-size:14.5px;color:var(--blue)}

/* footer */
.footer-brand{left:0;top:4300px;width:1200px;text-align:center;color:var(--white);font-size:30px;font-weight:700}
.footer-nav{left:0;top:4390px;width:1200px;display:flex;justify-content:center;gap:44px;font-size:15px;color:var(--white)}
.footer-social{left:490px;top:4450px}
.legal{left:117px;top:4538px;font-size:12px;color:var(--ink)}
</style>
</head>
<body>

<header class="site-header abs">
  <div class="brand abs">Brivo Australia Dental</div>
  <div class="social header-social abs"><span></span><span></span><span></span><span></span><span></span></div>
  <div class="call abs">
    <svg width="20" height="32" viewBox="0 0 20 32"><rect x="2" y="2" width="16" height="28" rx="3" fill="none" stroke="#fff" stroke-width="2"/><line x1="8" y1="25" x2="12" y2="25" stroke="#fff" stroke-width="2"/></svg>
    <div><div class="call-label">CALL US NOW</div><div class="call-number">0400 318 226</div></div>
  </div>
  <nav class="main-nav abs"><a class="current">Home</a><a>About Us</a><a>Projects</a><a>Get Involved</a><a>Contact Us</a></nav>
  <a class="nav-donate abs">DONATE</a>
</header>

<section>
  <div class="hero-photo abs" role="img" aria-label="Dentist treating a patient in a dental chair"></div>
  <svg class="abs" style="left:0;top:620px" width="1200" height="170" viewBox="0 0 1200 170">
    <path d="M0 85 C120 165 280 175 470 140 C700 100 950 30 1200 45 L1200 170 L0 170 Z" fill="var(--blue)"/>
    <path d="M0 70 C120 140 280 150 470 118 C700 80 950 22 1200 38 L1200 170 L0 170 Z" fill="#fff"/>
  </svg>
  <h1 class="hero-title abs">WELCOME TO<br>BRIVO</h1>
  <a class="btn-hero abs">GET STARTED</a>
  <div class="dots abs"><span></span><span></span><span></span></div>
</section>

<section>
  <h2 class="section-title abs" style="top:845px">OUR <em>MISSION</em></h2>
  <div class="rule abs" style="top:910px"></div>
  <p class="mission-text abs">Lorem ipsum dolor sit amet, consectetur adipiscing elit, sed do eiusmod tempor incididunt ut labore et dolore magna aliqua. Quis ipsum suspendisse ultrices gravida. Risus commodo viverra maecenas accumsan lacus vel facilisis. Lorem ipsum dolor sit amet, consectetur adipiscing elit, sed do eiusmod tempor incididunt ut labore et dolore magna aliqua. Quis ipsum suspendisse ultrices gravida. Risus commodo viverra maecenas accumsan lacus vel facilisis.</p>
  <a class="pill btn-mission abs">Read More <svg width="20" height="12" viewBox="0 0 20 12"><path d="M1 6H18M13 1L18 6L13 11" fill="none" stroke="#fff" stroke-width="2"/></svg></a>
</section>

<section>
  <div class="about-band abs"></div>
  <div class="about-photo abs" role="img" aria-label="Young girl having her teeth checked by a dentist"></div>
  <h2 class="about-title abs">ABOUT <em>US</em></h2>
  <div class="about-text abs">
    <p>Brivo Mobile Dental is a group of Dental Professionals who strongly believes anyone and anywhere can look healthy and fabulous with a bright Smile.</p>
    <p>Lorem ipsum dolor sit amet, consectetur adipiscing elit, sed do eiusmod tempor incididunt ut labore et dolore magna aliqua. Quis ipsum suspendisse ultrices gravida. Risus commodo viverra maecenas accumsan lacus vel facilisis.</p>
  </div>
  <a class="pill btn-about abs">Read More <svg width="20" height="12" viewBox="0 0 20 12"><path d="M1 6H18M13 1L18 6L13 11" fill="none" stroke="var(--blue)" stroke-width="2"/></svg></a>
</section>

<section>
  <h2 class="section-title abs" style="top:1923px">OUR <em>KEY VALUES</em></h2>
  <div class="rule abs" style="top:1998px"></div>
  <div class="value abs" style="left:79px;top:2075px">
    <div class="value-photo" role="img" aria-label="Smiling dental staff members"></div>
    <h3>PROFESSIONALISM</h3>
    <p>Our actions do the talking. Our caring and passionate staff will meet all your dental needs to ensure you are comfortable.</p>
    <div class="more">Read More <svg width="20" height="16" viewBox="0 0 20 16"><path d="M2 2L8 8L2 14M10 2L16 8L10 14" fill="none" stroke="var(--blue)" stroke-width="3"/></svg></div>
  </div>
  <div class="value abs" style="left:430px;top:2075px">
    <div class="value-photo" role="img" aria-label="Mobile dental clinic truck"></div>
    <h3>HONESTY</h3>
    <p>Our work is our purpose, our driving force. Our patients are our number one priority and we will help you through all your Dental needs.</p>
    <div class="more">Read More <svg width="20" height="16" viewBox="0 0 20 16"><path d="M2 2L8 8L2 14M10 2L16 8L10 14" fill="none" stroke="var(--blue)" stroke-width="3"/></svg></div>
  </div>
  <div class="value abs" style="left:777px;top:2075px">
    <div class="value-photo" role="img" aria-label="Dental chair inside the mobile clinic"></div>
    <h3>EDUCATION</h3>
    <p>Our purpose is to Educate anyone and everyone how to create and maintain their best Smile possible.</p>
    <div class="more">Read More <svg width="20" height="16" viewBox="0 0 20 16"><path d="M2 2L8 8L2 14M10 2L16 8L10 14" fill="none" stroke="var(--blue)" stroke-width="3"/></svg></div>
  </div>
</section>

<section>
  <div class="donate-dark abs"></div>
  <div class="donate-blue abs"></div>
  <h2 class="donate-title abs">Please donate to help a child</h2>
  <p class="donate-text abs">Lorem ipsum dolor sit amet, consectetur adipiscing elit, sed do eiusmod tempor incididunt ut labore et dolore magna aliqua. Quis ipsum suspendisse</p>
  <a class="pill btn-donate abs">DONATE NOW</a>
</section>

<section>
  <h2 class="section-title abs" style="top:2840px">OUR <em>SERVICES</em></h2>
  <div class="rule abs" style="top:2915px"></div>

  <div class="service-photo abs" style="left:112px;top:2993px;background:linear-gradient(135deg,#1e3a4a,#6f8a96 50%,#cfd8dc)" role="img" aria-label="Children colouring activity sheets with markers"></div>
  <h3 class="service-title abs" style="left:112px;top:3310px">Grow to Smile Program</h3>
  <ul class="service-list abs" style="left:112px;top:3376px;width:440px">
    <li><svg width="22" height="20" viewBox="0 0 22 20"><g fill="var(--blue)"><rect x="8" y="0" width="6" height="6" transform="rotate(45 11 3)"/><rect x="1" y="7" width="6" height="6" transform="rotate(45 4 10)"/><rect x="15" y="7" width="6" height="6" transform="rotate(45 18 10)"/><rect x="8" y="14" width="6" height="6" transform="rotate(45 11 17)"/></g></svg>Educational presentations and seminars for kids and parents to enjoy</li>
    <li><svg width="22" height="20" viewBox="0 0 22 20"><g fill="var(--blue)"><rect x="8" y="0" width="6" height="6" transform="rotate(45 11 3)"/><rect x="1" y="7" width="6" height="6" transform="rotate(45 4 10)"/><rect x="15" y="7" width="6" height="6" transform="rotate(45 18 10)"/><rect x="8" y="14" width="6" height="6" transform="rotate(45 11 17)"/></g></svg>Interactive games while learning the vital techniques and skills of maintaining healthy oral hygiene;</li>
    <li><svg width="22" height="20" viewBox="0 0 22 20"><g fill="var(--blue)"><rect x="8" y="0" width="6" height="6" transform="rotate(45 11 3)"/><rect x="1" y="7" width="6" height="6" transform="rotate(45 4 10)"/><rect x="15" y="7" width="6" height="6" transform="rotate(45 18 10)"/><rect x="8" y="14" width="6" height="6" transform="rotate(45 11 17)"/></g></svg>Interactive games while learning the vital techniques and skills of maintaining healthy oral hygiene;</li>
  </ul>

  <div class="service-photo abs" style="left:638px;top:2993px;background:linear-gradient(135deg,#f2f2f2,#b9bcbf 55%,#6d6f72)" role="img" aria-label="Soft striped pillows on a bed"></div>
  <h3 class="service-title abs" style="left:640px;top:3308px">Beautiful &amp; Retired Program</h3>
  <ul class="service-list abs" style="left:640px;top:3374px;width:460px">
    <li><svg width="22" height="20" viewBox="0 0 22 20"><g fill="var(--blue)"><rect x="8" y="0" width="6" height="6" transform="rotate(45 11 3)"/><rect x="1" y="7" width="6" height="6" transform="rotate(45 4 10)"/><rect x="15" y="7" width="6" height="6" transform="rotate(45 18 10)"/><rect x="8" y="14" width="6" height="6" transform="rotate(45 11 17)"/></g></svg>Our mobile services are performed within the spacious compounds of our State of the Art Mobile clinic:</li>
    <li><svg width="22" height="20" viewBox="0 0 22 20"><g fill="var(--blue)"><rect x="8" y="0" width="6" height="6" transform="rotate(45 11 3)"/><rect x="1" y="7" width="6" height="6" transform="rotate(45 4 10)"/><rect x="15" y="7" width="6" height="6" transform="rotate(45 18 10)"/><rect x="8" y="14" width="6" height="6" transform="rotate(45 11 17)"/></g></svg>Dental assessment and treatment services including simple check ups, scale &amp; polish, filling, gum treatment, crowns, implants, dentures, root canal therapy, fully licensed dental x-rays and other complex procedures.</li>
  </ul>
</section>

<section>
  <div class="map abs" role="img" aria-label="Map of central Australia showing the clinic location"></div>
  <div class="contact-card abs">
    <h3 class="card-title abs" style="top:48px">WORKING HOURS</h3>
    <table class="hours abs">
      <tr><td>MON – WED</td><td>8:00 AM – 7:00 PM</td></tr>
      <tr><td>THU 8:00 AM</td><td>5:00 PM</td></tr>
      <tr><td>FRI 8:00 AM</td><td>5:00 PM</td></tr>
      <tr><td>SAT</td><td>SUN CLOSED</td></tr>
    </table>
    <h3 class="card-title abs" style="top:288px">CONTACT DETAILS</h3>
    <div class="contact-row abs" style="top:348px"><svg width="18" height="24" viewBox="0 0 18 24"><path d="M9 1C4.6 1 1 4.5 1 9c0 6 8 14 8 14s8-8 8-14c0-4.5-3.6-8-8-8z" fill="var(--blue)"/><circle cx="9" cy="9" r="3" fill="#fff"/></svg>Level 12, 40 Harbour Lane Sydney NSW</div>
    <div class="contact-row abs" style="top:398px"><svg width="18" height="20" viewBox="0 0 18 20"><path d="M3 1l4 1 1 5-3 2c1 3 3 5 6 6l2-3 5 1 0 4c-1 2-3 2-5 2C7 18 1 12 1 5c0-2 0-3 2-4z" fill="var(--blue)"/></svg>Tel: 0400 318 226</div>
    <div class="contact-row abs" style="top:440px"><svg width="18" height="14" viewBox="0 0 18 14"><rect x="0" y="0" width="18" height="14" fill="var(--blue)"/><path d="M1 1L9 8L17 1" fill="none" stroke="#fff" stroke-width="1.5"/></svg>Email: hello@mobilesmilecare.com.au</div>
  </div>
</section>

<footer>
  <svg class="abs" style="left:0;top:4160px" width="1200" height="350" viewBox="0 0 1200 350">
    <path d="M0 100 C200 120 420 150 650 110 C850 75 1020 20 1200 10 L1200 350 L0 350 Z" fill="var(--blue)"/>
  </svg>
  <div class="footer-brand abs">Brivo Australia Dental</div>
  <nav class="footer-nav abs"><a>Home</a><a>About Us</a><a>Projects</a><a>Get Involved</a><a>Contact Us</a></nav>
  <div class="social footer-social abs"><span></span><span></span><span></span><span></span><span></span></div>
  <p class="legal abs">© 2019 All Rights Reserved | Privacy Policy | Terms and Conditions</p>
</footer>

</body>
</html>
```